Lorvex Tilo medical cannibis cultivation company

tag - Tilo rise
Lorvex Tilo medical cannabis cultivation - logo is selected- can we please see bold examples with our selection. We are mainly dealing with medical companies and professionals. We would like to be stand out in the crowd with our designs. Welcome any and all attempts. Thanks

Target Market(s)

Medical and Professional

Industry/Entity Type

Medical And Science

Font styles to use
Sans Serif

Colors

Designer to choose colors to be used in the design.

Requirements
Must have
• Bright colour and be bold- Love the teal and magenta that is currently on the dark background design.
Nice to have
• shading and the 3D affect- The shadowed appearance.
Should not have
• Anything related to illegal activity or un professional manners

```html
<!DOCTYPE html>
<html lang="en">
<head>
<meta charset="utf-8">
<title>Lorvex Tilo — Business Card</title>
<link rel="stylesheet" href="https://fonts.googleapis.com/css2?family=Roboto:wght@400;500;700&display=swap">
<style>
  :root {
    --page: #e4e4e4;
    --card: #000000;
    --teal: #00aee6;
    --magenta: #9c4a9b;
    --steel: #8a9197;
    --ink: #0c1a22;
    --white: #ffffff;
  }
  * { margin: 0; padding: 0; box-sizing: border-box; }
  html, body { width: 1125px; height: 1200px; overflow: hidden; }
  body {
    background: var(--page);
    font-family: "Roboto", Arial, sans-serif;
    position: relative;
  }
  .card {
    position: absolute;
    left: 150px;
    width: 825px;
    height: 470px;
    border-radius: 26px;
    background: var(--card);
    overflow: hidden;
  }
  .card--front { top: 98px; }
  .card--back { top: 630px; }
  .wave { position: absolute; inset: 0; width: 100%; height: 100%; }

  .brand {
    position: absolute;
    left: 48px;
    top: 52px;
    width: 280px;
    text-align: center;
  }
  .brand__ring {
    width: 150px; height: 150px;
    margin: 0 auto 12px;
    border: 5px solid var(--steel);
    border-radius: 50%;
  }
  .brand__name {
    font-weight: 500;
    font-size: 40px;
    letter-spacing: 1px;
    color: var(--teal);
    line-height: 1;
  }
  .brand__tag {
    display: flex; align-items: center; gap: 8px;
    margin-top: 6px;
    font-size: 18px;
    letter-spacing: 2px;
    color: var(--steel);
    text-transform: uppercase;
  }
  .brand__tag::before, .brand__tag::after {
    content: ""; flex: 1; height: 2px; background: var(--steel);
  }

  .contact {
    position: absolute;
    right: 52px;
    top: 228px;
    text-align: right;
    color: var(--ink);
  }
  .contact__name { font-weight: 700; font-size: 29px; letter-spacing: 0.5px; line-height: 1; }
  .contact__role { font-weight: 500; font-size: 20px; margin-top: 4px; }
  .contact__address { font-size: 19px; line-height: 25px; margin-top: 16px; }
  .contact__lines { list-style: none; margin-top: 12px; font-size: 19px; line-height: 27px; }
  .contact__lines li { display: flex; justify-content: flex-end; align-items: center; gap: 9px; }
  .contact__lines svg { width: 16px; height: 16px; fill: var(--ink); }

  .emblem {
    position: absolute;
    left: 50%; top: 104px;
    transform: translateX(-50%);
    width: 260px; height: 260px;
    border: 6px solid var(--steel);
    border-radius: 50%;
    display: flex; align-items: center; justify-content: center;
  }
  .emblem__name {
    font-weight: 500;
    font-size: 34px;
    letter-spacing: 1px;
    color: var(--teal);
  }
  .back__web {
    position: absolute;
    left: 0; right: 0; top: 408px;
    text-align: center;
    color: var(--white);
    font-size: 20px;
    letter-spacing: 4px;
  }
</style>
</head>
<body>
  <section class="card card--front">
    <svg class="wave" viewBox="0 0 800 455" preserveAspectRatio="none" aria-hidden="true">
      <path fill="var(--magenta)" d="M30,375 C180,395 320,330 440,250 C560,170 680,138 770,140 L800,146 L800,455 L0,455Z"/>
      <path fill="var(--steel)" d="M0,362 C150,392 320,345 445,266 C565,186 680,152 800,154 L800,455 L0,455Z"/>
      <path fill="#111" d="M0,392 C160,432 330,372 450,282 C570,194 690,158 800,157 L800,455 L0,455Z"/>
      <path fill="var(--teal)" d="M0,400 C160,440 330,382 456,290 C576,202 690,164 800,161 L800,455 L0,455Z"/>
    </svg>

    <div class="brand">
      <div class="brand__ring"></div>
      <div class="brand__name">LORVEX TILO</div>
      <div class="brand__tag">Tilo rise</div>
    </div>

    <div class="contact">
      <div class="contact__name">MARA KENDEL</div>
      <div class="contact__role">CEO/FOUNDER</div>
      <div class="contact__address">2140 Fernwood Court<br>Kettle Bay, Alaska 34518</div>
      <ul class="contact__lines">
        <li>512 804 3196
          <svg viewBox="0 0 24 24"><path d="M6.6 10.8a15.1 15.1 0 0 0 6.6 6.6l2.2-2.2c.3-.3.7-.4 1-.2 1.1.4 2.3.6 3.6.6.6 0 1 .4 1 1V20c0 .6-.4 1-1 1A17 17 0 0 1 3 4c0-.6.4-1 1-1h3.5c.6 0 1 .4 1 1 0 1.2.2 2.4.6 3.6.1.3 0 .7-.2 1z"/></svg>
        </li>
        <li>mara@lorvextilo.com
          <svg viewBox="0 0 24 24"><path d="M2 5h20v14H2z M2 5l10 7 10-7" fill="var(--ink)"/><path d="M3 6l9 6.3L21 6" fill="none" stroke="var(--teal)" stroke-width="1.6"/></svg>
        </li>
        <li>www.lorvextilo.com
          <svg viewBox="0 0 24 24"><circle cx="12" cy="12" r="10"/><path d="M2 12h20M12 2c3 3 3 17 0 20M12 2c-3 3-3 17 0 20" fill="none" stroke="var(--teal)" stroke-width="1.4"/></svg>
        </li>
      </ul>
    </div>
  </section>

  <section class="card card--back">
    <div class="emblem"><span class="emblem__name">LORVEX TILO</span></div>
    <div class="back__web">www.lorvextilorise.com</div>
  </section>
</body>
</html>
```